Tovel & Associates - London New Letting and Property Management Company *

Tovel & Associates LTD is a new company based in London, and works with brand new residential property in the city centre.

We are aiming to have 1000 new properties a year.

We are looking for something modern and minimalistic :
Logo ,Monogram, Paper Head and Business Card.

Target Market(s)

Internation landlords

Industry/Entity Type

Real Estate

Logo Text

Tovel & Associates

Colors

Designer to choose colors to be used in the design.

Requirements
Nice to have
• A particular monogram with "TA"
Should not have
• Little House over the logo

```html
<!DOCTYPE html>
<html lang="en">
<head>
<meta charset="utf-8">
<title>Tovel &amp; Associates – Stationery</title>
<link rel="stylesheet" href="https://fonts.googleapis.com/css2?family=Montserrat:wght@400;500;600&display=swap">
<style>
  :root {
    --bg: #efefef;
    --paper: #ffffff;
    --coral: #f4956f;
    --coral-deep: #f08660;
    --coral-line: #f6b79c;
    --ink: #2b2b2b;
    --ink-soft: #555555;
    --slate: #2b3238;
    --flap-light: #e4e4e4;
    --font: "Montserrat", Arial, sans-serif;
  }
  * { box-sizing: border-box; margin: 0; padding: 0; }
  html, body { width: 1200px; height: 1200px; overflow: hidden; }
  body { background: var(--bg); font-family: var(--font); color: var(--ink); position: relative; }

  .sheet { position: absolute; background: var(--paper); box-shadow: 0 2px 8px rgba(0,0,0,.08); overflow: hidden; }

  /* Letterhead */
  .letterhead { left: 40px; top: 200px; width: 400px; height: 566px; }
  .rule { position: absolute; background: var(--coral-line); }
  .letterhead .rule-h { left: 0; right: 0; top: 92px; height: 1px; }
  .letterhead .rule-v { left: 106px; top: 0; bottom: 0; width: 1px; }
  .brand-small { position: absolute; left: 14px; top: 52px; width: 84px; font-size: 9px; font-weight: 600; color: var(--coral); line-height: 1.2; }
  .contact { position: absolute; right: 22px; top: 22px; list-style: none; font-size: 6px; color: var(--ink-soft); }
  .contact li { display: flex; align-items: center; gap: 5px; margin-bottom: 4px; }
  .dot { width: 7px; height: 7px; border-radius: 50%; background: var(--coral); flex: none; }
  .date { position: absolute; right: 22px; top: 76px; font-size: 6.5px; }
  .letter-body { position: absolute; left: 120px; top: 118px; right: 26px; font-size: 7px; line-height: 1.5; }
  .letter-body p { margin-bottom: 9px; }
  .signature-line { width: 60px; height: 1px; background: var(--ink); margin: 16px 0 4px; }
  .signer { font-weight: 600; font-size: 7.5px; }
  .signer-role { font-size: 6.5px; color: var(--ink-soft); }
  .footer-band { position: absolute; right: 0; bottom: 26px; width: 180px; height: 12px; background: var(--coral); }
  .web { position: absolute; left: 12px; bottom: 14px; display: flex; align-items: center; gap: 5px; font-size: 6.5px; }

  /* Cover sheet */
  .cover { left: 470px; top: 200px; width: 400px; height: 566px; }
  .cover .rule-h { left: 0; right: 0; top: 96px; height: 1px; }
  .cover .rule-v { left: 300px; top: 0; bottom: 0; width: 1px; }
  .brand-large { position: absolute; left: 40px; bottom: 80px; width: 240px; font-size: 32px; font-weight: 500; color: var(--coral); line-height: 1.1; }

  /* Business cards */
  .card { position: absolute; width: 260px; height: 150px; background: linear-gradient(135deg, var(--coral), var(--coral-deep)); box-shadow: 0 2px 6px rgba(0,0,0,.1); overflow: hidden; color: #fff; }
  .card-front { left: 900px; top: 200px; display: flex; align-items: center; justify-content: center; }
  .card-front .brand-card { font-size: 16px; font-weight: 500; }
  .card-back { left: 900px; top: 370px; }
  .card-back .rule { background: rgba(255,255,255,.6); }
  .card-back .rule-h { left: 0; right: 0; top: 44px; height: 1px; }
  .card-back .rule-v { left: 96px; top: 0; bottom: 0; width: 1px; }
  .card-back .brand-card { position: absolute; left: 10px; top: 14px; font-size: 9px; font-weight: 500; width: 80px; }
  .card-details { position: absolute; left: 108px; top: 56px; font-size: 6.5px; line-height: 1.6; }
  .card-details .name { font-weight: 600; font-size: 8px; }
  .card-web { position: absolute; left: 10px; bottom: 10px; font-size: 6px; }

  /* Envelope */
  .envelope { position: absolute; left: 900px; top: 545px; width: 260px; height: 170px; background: var(--slate); box-shadow: 0 2px 6px rgba(0,0,0,.12); }
  .envelope svg { position: absolute; left: 0; top: 0; }

  /* Compliment card */
  .compliment { left: 900px; top: 735px; height: 170px; display: flex; align-items: center; justify-content: center; }
  .compliment .brand-card { font-size: 18px; font-weight: 500; }
</style>
</head>
<body>

<article class="sheet letterhead">
  <div class="rule rule-h"></div>
  <div class="rule rule-v"></div>
  <div class="brand-small">Tovel &amp; Associates</div>
  <ul class="contact">
    <li><span class="dot"></span>+44 (0) 20 7946 0321</li>
    <li><span class="dot"></span>info@tovelassociates.co.uk</li>
    <li><span class="dot"></span>12 Harlow Street, London</li>
  </ul>
  <div class="date">09 November 2018</div>
  <div class="letter-body">
    <p>Hello Mr Hollis,</p>
    <p>I noticed that you have had your home for sale by owner for 4 weeks and was wondering if I could be of any assistance. I recently sold homes in the neighborhood at Ashby Street and have active buyers looking in the area.</p>
    <p>I understand that saving on the commission is probably very important to you. I bet you didn't know that homes that sell with a real estate agent get a higher overall price than those that sold without one... often making up for the difference. I am hoping that we could work together, get the right price on your home and get your home sold.</p>
    <p>Call or text me at +44 (0) 20 7946 0321. We'll set up time, and I'm happy to share my ideas and marketing strategy to get your home sold fast.</p>
    <p>Best Regards</p>
    <div class="signature-line"></div>
    <div class="signer">Nora Vale</div>
    <div class="signer-role">Managing Director, Tovel &amp; Associates LTD</div>
  </div>
  <div class="footer-band"></div>
  <div class="web"><span class="dot"></span>tovelassociates.co.uk</div>
</article>

<article class="sheet cover">
  <div class="rule rule-h"></div>
  <div class="rule rule-v"></div>
  <div class="brand-large">Tovel &amp; Associates</div>
</article>

<section class="card card-front">
  <span class="brand-card">Tovel &amp; Associates</span>
</section>

<section class="card card-back">
  <div class="rule rule-h"></div>
  <div class="rule rule-v"></div>
  <span class="brand-card">Tovel &amp; Associates</span>
  <div class="card-details">
    <div class="name">Nora Vale</div>
    <div>Managing Director</div>
    <div>+44 (0) 20 7946 0321</div>
    <div>info@tovelassociates.co.uk</div>
    <div>12 Harlow Street, London</div>
  </div>
  <div class="card-web">tovelassociates.co.uk</div>
</section>

<section class="envelope">
  <svg width="260" height="170" viewBox="0 0 260 170">
    <polygon points="0,0 260,0 260,22 0,52" fill="#f4956f"/>
    <polygon points="0,52 260,22 260,34 10,64" fill="#e4e4e4"/>
  </svg>
</section>

<section class="card compliment">
  <span class="brand-card">Tovel &amp; Associates</span>
</section>

</body>
</html>
```